Redesign of Medical App for Patients

• The Designer’s task is to provide a new fully-responsive design for our apps, and then code it using only basic html and CSS.
• Your design will be incorporated into our existing REACT native app.

Target Market(s)

Medical Patients

Industry/Entity Type

Medical

Coding

Coded - Design and coding required

Number of Pages Required

5+ page

Requirements
Must have
• Short list candidates will receive detailed briefing
Nice to have
• detailed briefing contains some of our ideas.

```html
<!DOCTYPE html>
<html lang="en">
<head>
<meta charset="utf-8">
<title>Kindrela – Patient App Screens</title>
<link rel="stylesheet" href="https://fonts.googleapis.com/css2?family=Exo+2:wght@400;500;600;700&display=swap">
<style>
  :root{
    --stage:#4d4d4d;
    --screen:#eef6fb;
    --ink:#111c24;
    --muted:#8a9aa6;
    --blue:#2a86bd;
    --blue-deep:#1d6c9c;
    --orange:#f37021;
    --card:#ffffff;
    --card-text:#3b4a55;
  }
  *{box-sizing:border-box;margin:0;padding:0}
  html,body{width:1200px;height:722px;overflow:hidden;background:var(--stage);font-family:"Exo 2",sans-serif;color:var(--ink)}
  .canvas{position:relative;width:1200px;height:722px}
  .screen{position:absolute;width:246px;height:532px;background:var(--screen);border-radius:28px;overflow:hidden}
  .screen--pre{left:92px;top:84px}
  .screen--proc{left:465px;top:84px}
  .screen--rec{left:851px;top:75px}

  .header{position:absolute;left:0;top:0;width:246px;height:170px}
  .status-time{position:absolute;left:22px;top:10px;color:#fff;font-size:10px;font-weight:500}
  .brand{position:absolute;left:25px;top:84px;display:flex;align-items:center;gap:8px}
  .brand-dot{width:36px;height:36px;border-radius:50%;background:#fff;flex:none}
  .brand-name{color:#fff;font-weight:700;font-size:28px;letter-spacing:-.3px;line-height:1}

  .title{position:absolute;left:7px;top:172px;font-size:25px;font-weight:600;color:var(--ink);line-height:1.2}

  .pill{position:absolute;top:218px;height:31px;border-radius:16px;color:#fff;font-size:12.5px;font-weight:500;display:flex;align-items:center;justify-content:center;box-shadow:0 2px 4px rgba(0,0,0,.12)}
  .pill--weeks{left:7px;width:103px;background:var(--orange)}
  .pill--days{left:124px;width:89px;background:var(--blue)}
  .check-note{position:absolute;left:7px;top:269px;display:flex;align-items:center;gap:6px;font-size:10px;font-weight:500}

  .task{position:absolute;width:70px;height:57px;background:var(--card);border-radius:5px;box-shadow:0 1px 4px rgba(30,80,120,.1);text-align:center;font-size:7.3px;line-height:1.3;color:var(--card-text);padding-top:8px}
  .task-dot{width:18px;height:18px;border-radius:50%;background:var(--blue);margin:0 auto 5px}

  .stage-card{position:absolute;left:7px;width:233px;height:73px;border-radius:6px;overflow:hidden}
  .stage-photo{position:absolute;inset:0;background:linear-gradient(120deg,#cfe3ee 0%,#7fb6d3 45%,#2f86b7 75%,#1f6f9e 100%)}
  .stage-label{position:absolute;left:8px;bottom:7px;color:#fff;font-size:8px;font-weight:600}
  .stage-arrow{position:absolute;right:8px;bottom:9px}

  .tile{position:absolute;width:69px;height:56px;background:var(--card);border-radius:5px;box-shadow:0 1px 4px rgba(30,80,120,.1);text-align:center;font-size:7px;line-height:1.3;color:var(--card-text);padding-top:5px}
  .tile svg{display:block;margin:0 auto 2px}

  .nav{position:absolute;left:0;bottom:0;width:246px;height:57px;background:#fff;border-radius:16px 16px 0 0}
  .nav-item{position:absolute;top:17px;width:40px;margin-left:-20px;text-align:center;font-size:7.5px;color:var(--muted)}
  .nav-item svg{display:block;margin:0 auto 1px}
  .nav-item--active{color:var(--blue)}
</style>
</head>
<body>
<div class="canvas">

  <!-- Pre-procedure -->
  <section class="screen screen--pre">
    <svg class="header" viewBox="0 0 246 170" role="img" aria-label="Photo of a surgical nurse in a clinic, blue tinted">
      <defs><linearGradient id="hdrA" x1="0" y1="0" x2="1" y2="1"><stop offset="0" stop-color="#4e9fcb"/><stop offset="1" stop-color="#1f6f9e"/></linearGradient></defs>
      <path d="M0 0H246V125Q246 147 220 150L45 152Q12 155 0 165Z" fill="url(#hdrA)"/>
    </svg>
    <div class="status-time">9:30</div>
    <div class="brand"><span class="brand-dot"></span><span class="brand-name">KINDRELA</span></div>
    <h1 class="title">Pre-procedure</h1>
    <div class="pill pill--weeks">Weeks Before</div>
    <div class="pill pill--days">Days Before</div>
    <div class="check-note">
      <svg width="14" height="14" viewBox="0 0 14 14"><circle cx="7" cy="7" r="6" fill="none" stroke="#111c24" stroke-width="1.1"/><path d="M4 7.2l2 2 4-4" fill="none" stroke="#111c24" stroke-width="1.1"/></svg>
      Check When Task is Complete
    </div>
    <div class="task" style="left:7px;top:298px"><div class="task-dot"></div>Pre-operative<br>appointment</div>
    <div class="task" style="left:89px;top:298px"><div class="task-dot"></div>8 th<br>weeks before</div>
    <div class="task" style="left:170px;top:298px"><div class="task-dot"></div>6 th<br>weeks before</div>
    <div class="task" style="left:7px;top:368px"><div class="task-dot"></div>2 nd<br>weeks before</div>
    <div class="task" style="left:89px;top:368px"><div class="task-dot"></div>1 st<br>week before</div>
    <nav class="nav">
      <div class="nav-item nav-item--active" style="left:18px"><svg width="14" height="13" viewBox="0 0 14 13"><path d="M7 1L1 6.5h2V12h3V8.5h2V12h3V6.5h2Z" fill="currentColor"/></svg>Home</div>
      <div class="nav-item" style="left:82px"><svg width="13" height="13" viewBox="0 0 13 13"><circle cx="5.5" cy="5.5" r="4" fill="none" stroke="#111c24" stroke-width="1.6"/><path d="M8.5 8.5L12 12" stroke="#111c24" stroke-width="1.8"/></svg>Search</div>
      <div class="nav-item" style="left:156px"><svg width="22" height="13" viewBox="0 0 22 13"><circle cx="5" cy="3" r="2.3" fill="#111c24"/><circle cx="11" cy="2.8" r="2.6" fill="#111c24"/><circle cx="17" cy="3" r="2.3" fill="#111c24"/><path d="M1 12q0-6 4-6t4 6Z M6.5 13q0-7 4.5-7t4.5 7Z M13 12q0-6 4-6t4 6Z" fill="#111c24"/></svg>Team</div>
      <div class="nav-item" style="left:222px"><svg width="13" height="13" viewBox="0 0 13 13"><circle cx="6.5" cy="6.5" r="4.5" fill="none" stroke="#111c24" stroke-width="3" stroke-dasharray="2.2 1.3"/><circle cx="6.5" cy="6.5" r="1.6" fill="#fff"/></svg>Setting</div>
    </nav>
  </section>

  <!-- Procedure -->
  <section class="screen screen--proc">
    <svg class="header" viewBox="0 0 246 170" role="img" aria-label="Photo of a doctor with a patient in a ward, blue tinted">
      <defs><linearGradient id="hdrB" x1="0" y1="0" x2="1" y2="1"><stop offset="0" stop-color="#4e9fcb"/><stop offset="1" stop-color="#1f6f9e"/></linearGradient></defs>
      <path d="M0 0H246V125Q246 147 220 150L45 152Q12 155 0 165Z" fill="url(#hdrB)"/>
    </svg>
    <div class="status-time">9:30</div>
    <div class="brand"><span class="brand-dot"></span><span class="brand-name">KINDRELA</span></div>
    <h1 class="title">Procedure</h1>
    <div class="stage-card" style="top:213px"><div class="stage-photo" role="img" aria-label="Photo of a nurse preparing a hospital bed"></div><span class="stage-label">Preparation</span><svg class="stage-arrow" width="11" height="5" viewBox="0 0 11 5"><path d="M0 2.5h10M8 .5l2 2-2 2" fill="none" stroke="#fff" stroke-width=".9"/></svg></div>
    <div class="stage-card" style="top:296px"><div class="stage-photo" role="img" aria-label="Photo of a nurse assisting an elderly patient"></div><span class="stage-label">What Happens?</span><svg class="stage-arrow" width="11" height="5" viewBox="0 0 11 5"><path d="M0 2.5h10M8 .5l2 2-2 2" fill="none" stroke="#fff" stroke-width=".9"/></svg></div>
    <div class="stage-card" style="top:381px"><div class="stage-photo" role="img" aria-label="Photo of medical staff moving a patient on a gurney"></div><span class="stage-label">Immediately after</span><svg class="stage-arrow" width="11" height="5" viewBox="0 0 11 5"><path d="M0 2.5h10M8 .5l2 2-2 2" fill="none" stroke="#fff" stroke-width=".9"/></svg></div>
    <nav class="nav">
      <div class="nav-item nav-item--active" style="left:18px"><svg width="14" height="13" viewBox="0 0 14 13"><path d="M7 1L1 6.5h2V12h3V8.5h2V12h3V6.5h2Z" fill="currentColor"/></svg>Home</div>
      <div class="nav-item" style="left:82px"><svg width="13" height="13" viewBox="0 0 13 13"><circle cx="5.5" cy="5.5" r="4" fill="none" stroke="#111c24" stroke-width="1.6"/><path d="M8.5 8.5L12 12" stroke="#111c24" stroke-width="1.8"/></svg>Search</div>
      <div class="nav-item" style="left:156px"><svg width="22" height="13" viewBox="0 0 22 13"><circle cx="5" cy="3" r="2.3" fill="#111c24"/><circle cx="11" cy="2.8" r="2.6" fill="#111c24"/><circle cx="17" cy="3" r="2.3" fill="#111c24"/><path d="M1 12q0-6 4-6t4 6Z M6.5 13q0-7 4.5-7t4.5 7Z M13 12q0-6 4-6t4 6Z" fill="#111c24"/></svg>Team</div>
      <div class="nav-item" style="left:222px"><svg width="13" height="13" viewBox="0 0 13 13"><circle cx="6.5" cy="6.5" r="4.5" fill="none" stroke="#111c24" stroke-width="3" stroke-dasharray="2.2 1.3"/><circle cx="6.5" cy="6.5" r="1.6" fill="#fff"/></svg>Setting</div>
    </nav>
  </section>

  <!-- Recovery -->
  <section class="screen screen--rec">
    <svg class="header" viewBox="0 0 246 170" role="img" aria-label="Photo of a nurse caring for a smiling elderly patient, blue tinted">
      <defs><linearGradient id="hdrC" x1="0" y1="0" x2="1" y2="1"><stop offset="0" stop-color="#4e9fcb"/><stop offset="1" stop-color="#1f6f9e"/></linearGradient></defs>
      <path d="M0 0H246V125Q246 147 220 150L45 152Q12 155 0 165Z" fill="url(#hdrC)"/>
    </svg>
    <div class="status-time">9:30</div>
    <div class="brand"><span class="brand-dot"></span><span class="brand-name">KINDRELA</span></div>
    <h1 class="title">Recovery</h1>
    <div class="tile" style="left:7px;top:211px"><svg width="26" height="24" viewBox="0 0 26 24" fill="none" stroke="#2a86bd" stroke-width="1.2"><path d="M2 22V9M2 17h22v5M24 17v-4H10v4M5 14a2 2 0 1 0 0.1 0"/><path d="M13 10V6h6V3l5 4-5 4V8h-4"/></svg>When do i leave<br>the hospital?</div>
    <div class="tile" style="left:89px;top:211px"><svg width="24" height="24" viewBox="0 0 24 24" fill="none" stroke="#2a86bd" stroke-width="1.2"><circle cx="12" cy="13" r="8"/><path d="M12 8v5l3 2M5 4l3-2M19 4l-3-2"/></svg>Waking<br>Up</div>
    <div class="tile" style="left:171px;top:211px"><svg width="24" height="24" viewBox="0 0 24 24" fill="none" stroke="#2a86bd" stroke-width="1.2"><path d="M12 2v20M8 6h8M7 10h10M8 14h8M9 18h6"/><circle cx="12" cy="12" r="3"/></svg>Pain<br>Mangement</div>
    <div class="tile" style="left:7px;top:281px"><svg width="24" height="24" viewBox="0 0 24 24" fill="none" stroke="#2a86bd" stroke-width="1.2"><path d="M4 2h9v20H4ZM13 4l-4 2v14l4 2"/><path d="M15 12h7M19 9l3 3-3 3"/></svg>Same-day<br>Discharge</div>
    <div class="tile" style="left:89px;top:281px"><svg width="24" height="24" viewBox="0 0 24 24" fill="none" stroke="#2a86bd" stroke-width="1.2"><circle cx="12" cy="12" r="10"/><path d="M12 5c-4 5-4 9 0 13 4-4 4-8 0-13ZM12 8v12"/></svg>Ready to<br>Leave</div>
    <nav class="nav">
      <div class="nav-item nav-item--active" style="left:18px"><svg width="14" height="13" viewBox="0 0 14 13"><path d="M7 1L1 6.5h2V12h3V8.5h2V12h3V6.5h2Z" fill="currentColor"/></svg>Home</div>
      <div class="nav-item" style="left:82px"><svg width="13" height="13" viewBox="0 0 13 13"><circle cx="5.5" cy="5.5" r="4" fill="none" stroke="#111c24" stroke-width="1.6"/><path d="M8.5 8.5L12 12" stroke="#111c24" stroke-width="1.8"/></svg>Search</div>
      <div class="nav-item" style="left:156px"><svg width="22" height="13" viewBox="0 0 22 13"><circle cx="5" cy="3" r="2.3" fill="#111c24"/><circle cx="11" cy="2.8" r="2.6" fill="#111c24"/><circle cx="17" cy="3" r="2.3" fill="#111c24"/><path d="M1 12q0-6 4-6t4 6Z M6.5 13q0-7 4.5-7t4.5 7Z M13 12q0-6 4-6t4 6Z" fill="#111c24"/></svg>Team</div>
      <div class="nav-item" style="left:222px"><svg width="13" height="13" viewBox="0 0 13 13"><circle cx="6.5" cy="6.5" r="4.5" fill="none" stroke="#111c24" stroke-width="3" stroke-dasharray="2.2 1.3"/><circle cx="6.5" cy="6.5" r="1.6" fill="#fff"/></svg>Setting</div>
    </nav>
  </section>

</div>
</body>
</html>
```